Residential Remodeling Contractor needs updated business card

I need a new design for my business card.
Name of the company is Ridgefell Construction. I need a card that commands presence, strength, integrity. I have been in business for 28 years. I am a Residential Remodeling Contractor that covers all aspects of a residential remodel and build.

```html
<!DOCTYPE html>
<html lang="en">
<head>
<meta charset="utf-8">
<title>Ridgefell Construction – Business Card</title>
<link rel="stylesheet" href="https://fonts.googleapis.com/css2?family=Cinzel:wght@500;600&family=Poppins:wght@400;500&display=swap">
<style>
  :root {
    --brand-blue: #1f3c85;
    --accent-blue: #2f55b8;
    --paper: #ffffff;
    --ink-dark: #2a2a2a;
    --rule-grey: #b9b9b9;
    --backdrop: #e6e7ea;
  }
  * { box-sizing: border-box; margin: 0; padding: 0; }
  html, body { width: 1200px; height: 689px; overflow: hidden; }
  body { background: var(--backdrop); position: relative; font-family: "Poppins", sans-serif; }

  .card {
    position: absolute;
    top: 190px;
    width: 540px;
    height: 309px;
    border-radius: 22px;
    overflow: hidden;
    box-shadow: 0 10px 28px rgba(0,0,0,0.18);
  }
  .card--back { left: 40px; }
  .card--front { left: 620px; background: var(--paper); }

  .back-pattern { position: absolute; inset: 0; background: var(--brand-blue); }

  .brand {
    position: absolute; left: 30px; top: 92px;
    font-family: "Cinzel", serif; font-weight: 600;
    color: var(--brand-blue); line-height: 1.05;
    font-size: 25px; letter-spacing: 0.3px;
    white-space: nowrap;
  }
  .brand span { display: block; }

  .divider {
    position: absolute; left: 268px; top: 30px;
    width: 1px; height: 170px; background: var(--rule-grey);
  }

  .contact { position: absolute; left: 290px; top: 30px; color: var(--ink-dark); white-space: nowrap; }
  .contact__name {
    font-family: "Cinzel", serif; font-weight: 600;
    color: var(--brand-blue); font-size: 21px; line-height: 1;
  }
  .contact__title { font-size: 13px; margin-bottom: 12px; }
  .contact__row { display: flex; align-items: center; gap: 8px; font-size: 12.5px; line-height: 1.6; }
  .contact__row svg { width: 12px; height: 12px; fill: var(--brand-blue); flex: none; }
  .contact__row .hl { color: var(--accent-blue); }
  .contact__address { font-size: 12.5px; line-height: 1.35; margin-top: 8px; padding-left: 20px; }

  .band { position: absolute; left: 0; bottom: 0; width: 540px; height: 110px; }
  .band__text {
    position: absolute; left: 26px; bottom: 14px;
    color: var(--paper); transform: rotate(-2.7deg); transform-origin: left bottom;
    white-space: nowrap;
  }
  .band__since { font-size: 13px; line-height: 1.3; }
  .band__line { font-size: 11.5px; font-weight: 500; letter-spacing: 0.4px; line-height: 1.3; }
</style>
</head>
<body>

  <div class="card card--back">
    <div class="back-pattern" role="img" aria-label="Repeating embossed brand pattern on deep blue card back"></div>
  </div>

  <div class="card card--front">
    <div class="brand">
      <span>Ridgefell</span>
      <span>Construction</span>
    </div>

    <div class="divider"></div>

    <div class="contact">
      <div class="contact__name">Marcus Hale</div>
      <div class="contact__title">Managing Director</div>
      <div class="contact__row">
        <svg viewBox="0 0 24 24"><path d="M6.6 10.8a15.1 15.1 0 0 0 6.6 6.6l2.2-2.2a1 1 0 0 1 1-.25 11.4 11.4 0 0 0 3.6.6 1 1 0 0 1 1 1V20a1 1 0 0 1-1 1A17 17 0 0 1 3 4a1 1 0 0 1 1-1h3.5a1 1 0 0 1 1 1c0 1.25.2 2.45.6 3.6a1 1 0 0 1-.25 1z"/></svg>
        <span>044-555 010 233</span>
      </div>
      <div class="contact__row">
        <svg viewBox="0 0 24 24"><path d="M2 5h20v14H2z M2 5l10 8 10-8" stroke="#fff" stroke-width="1.5"/></svg>
        <span>info@ridgefell.com</span>
      </div>
      <div class="contact__row">
        <svg viewBox="0 0 24 24"><circle cx="12" cy="12" r="10"/><path d="M2 12h20M12 2c3 3 3 17 0 20M12 2c-3 3-3 17 0 20" stroke="#fff" stroke-width="1.3" fill="none"/></svg>
        <span>www.<span class="hl">ridgefellbuild</span>.com</span>
      </div>
      <div class="contact__address">
        17, Harbor Lane, Easton<br>45210, Westland
      </div>
    </div>

    <svg class="band" viewBox="0 0 540 110" preserveAspectRatio="none">
      <polygon points="0,26 540,0 540,110 0,110" fill="var(--brand-blue)"/>
    </svg>
    <div class="band__text">
      <div class="band__since">Since 28 years</div>
      <div class="band__line">RESIDENTIAL CONTRACTOR FOR REMODELING AND BUILD</div>
    </div>
  </div>

</body>
</html>
```